Velvet Ladle Wishes Website Design; Cupcake Business with a unique and bespoke design element

We need a website design for a new bespoke and unique business making gourmet cupcakes - but MOST IMPORTANTLY we design and handmake cupcake wrappers and toppers specifically for each client's event. We are based in Sydney, Australia. The final resulting website should be elegant yet whimsical reflecting the notion of dreams and very elegant events eg weddings and very special parties.

We want to eventually have about 5 pages, HOWEVER, this project is specifically for the first page (ie Home page) and one other only. The final required pages are: a HOME page; ABOUT US page; PHOTO GALLERY page; FLAVOUR MENU & OTHER PRODUCTS page; CONTACT & INTERNET ENQUIRY page.

We expect the HOME page to be quite elaborate, perhaps including some animation. We will be providing the text content for all the other pages, and basically they will have the same background as the home page. We are looking for a clean design that runs across each page thus giving the website a continuity that pulls it all together. We would like our logo to be included on each page.

PLEASE NOTE: We will want multiple pages worked on in the handover phase but initially we want a very concise, consistent template to limit the amount of work to prospective designers.

While we are primarily looking for the design phase to be covered by this project, we would certainly appreciate coding to be included and will take that into consideration when choosing a winner.
Updates

Hi Designers

We have added some more information to our brief - please review it.

Thanks and happy designing

Hi Designers

Please note that we have increased our Prize money to $750.00.  We hope this encourages you to participate.

Thanks and regards
Velvet Ladle Wishes

Hi Designers

We've just posted some photos to help give you an idea of what we do.  Please note our attention to detail and precision in our work.

Thanks
Velvet Ladle Wishes

Hi Designers

Please Note:  What makes us different  to any other cupcake business is that we design cupcake wrappers and toppers, unique to our client's event whether it be a wedding, a birthday party or product launch.  We consult with our client to understand themes, colours, styles etc.  We then have our designs printed, next they are cut by a specialised computerised cutting machine,  We assemble everything by hand, and usually embellish the wrapper and topper with pearls, crystals, feathers, lace, ribbons or whatever else is appropriate for the event.  All work is totally bespoke, unique and individual.  No other cupcake supplier that we know of goes to these lengths to satisfy their client's dreams.

THE WRAPPER AND TOPPER IS OUR PRIMARY SELLING POINT. 

PLEASE NOTE:- We have uploaded a new photograph which we want to be used as the main photograph on the landing page.

We have removed all previous photographs of cupcakes (except for one that we can't get rid of).

We don't want a picture of a cupcake on the landing page we want the image _D7C3239.jpg to be used for that purpose.

We have also uploaded our logo in a number of file formats as we have had requests from you for these.

Hi designers

we have a crazy busy weekend on and won't be able to make any decisions re our competition until Monday  -  sorry to keep you in suspense, just a couple more days please!

regards
Pam

Target Market(s)

Primarily women - brides, new mothers (Christenings), Event Planners, who place an emphasis on the beauty of a product rather than the cost

Industry/Entity Type

Events

Requirements
Must have
• It must have our Logo (see attached upload) on each page (our logo is a butterfly atop a cupcake resting on a spoon and our motto is "Creating Delicious Works of Art". The colours used are pale pink, blue and chocolate brown and we'd expect these colours to be repeated in the final website.
The website must have a photo gallery which we can access and add to/change as our business grows.
We need a contact page which has an "internet enquiry form".
There should be a "Menu" page describing our cupcake flavours.
The Home page must have a party/event feel to it - definitely making an enquirer want to enter further into the site.
Nice to have
• Our logo is attached below in the "uploads". One idea that we have had is to use the butterfly in the logo but start it as a caterpillar crawling on the screen; as it spins it's cocoon the words "Sweet Dreams Little Caterpillar" would appear on screen; this would incorporate the "Dreams" in our Business Name; then our logo butterfly would hatch. This encapsulates the idea of taking something plain (caterpillar/cupcake) and creating something beautiful (butterfly/OUR cupcake).
However, we are open to other design ideas.
The colours we would like to have are pale pink, blue and chocolate brown in the design.

Some websites we really admire are: www.mirabellhart.com www.ribbonglitterloaf.com.au and www.greetingsoriel.com.au
These websites have a lightness and sense of fantasy to them. They do not convey a corporate image at all, rather they make you want to be at the party.
Should not have
• No "Corporate" style.

Most Important: We already have a website which we are not happy with - that is why we are going through this exercise to replace it. That means we DO NOT want anything along the lines of our current website. We are expecting some fresh ideas for our prize money.

```html
<!DOCTYPE html>
<html lang="en">
<head>
<meta charset="utf-8">
<title>Velvet Ladle Wishes — Home</title>
<link href="https://fonts.googleapis.com/css2?family=Cabin:wght@400;500&family=Almendra:wght@700&family=Parisienne&display=swap" rel="stylesheet">
<style>
:root{
  --bg-pink:#f7cbd0;
  --page-pink:#fbdde1;
  --band-pink:#f8c2c6;
  --nav-brown:#5c3a41;
  --nav-dark:#3f2227;
  --nav-light:#75525a;
  --footer-brown:#4f2b32;
  --footer-inner:#5a333b;
  --heading-blue:#2f6d9a;
  --accent-pink:#e2176a;
  --chocolate:#5a2e14;
  --body-text:#4a2e2e;
  --featured:#f9aaae;
  --standard:#67a2c9;
  --white:#ffffff;
}
*{margin:0;padding:0;box-sizing:border-box}
html,body{width:1200px;height:1025px;overflow:hidden}
body{background:var(--bg-pink);font-family:'Cabin',sans-serif;color:var(--body-text);position:relative}
.page{position:absolute;left:155px;top:0;width:890px;height:1025px;background:var(--page-pink)}
.search{position:absolute;left:773px;top:14px;display:flex;align-items:center;gap:8px;font-size:14px;color:#6a5656}
.search-field{width:165px;height:23px;background:#a88e92;border:1px solid #8a7074}
.search-go{width:29px;height:23px;background:#6aaad9;color:var(--white);font-size:14px;display:flex;align-items:center;justify-content:center;margin-left:-4px}
.ribbon{position:absolute;top:0;left:0}
.nav{position:absolute;left:122px;top:52px;width:956px;height:43px;background:var(--nav-brown);border:2px solid var(--nav-dark);box-shadow:0 4px 6px rgba(60,30,35,.35)}
.nav-inner{position:absolute;inset:4px;border:1px solid var(--nav-light)}
.nav ul{list-style:none;position:absolute;left:121px;top:8px;display:flex;font-family:'Almendra',serif;font-size:14px;color:#f7ecec}
.nav li{padding:2px 19px;margin-right:8px}
.nav li.active{background:var(--nav-dark);margin-right:16px}
.hero{position:absolute;left:155px;top:95px;width:890px;height:290px;background:linear-gradient(90deg,#f8c7cd 0%,#f6c0c6 50%,#cdb5ad 100%)}
.hero-photo{position:absolute;left:420px;top:0;width:470px;height:290px;background:radial-gradient(circle at 70% 45%,#6e5c55 0%,#b6a399 40%,rgba(230,200,200,.0) 95%)}
.brand{position:absolute;left:60px;top:195px;display:flex;align-items:center;gap:12px}
.brand-mark{width:22px;height:22px;border-radius:50%;background:var(--accent-pink)}
.brand-name{font-family:'Cabin',sans-serif;font-weight:500;font-size:44px;color:var(--chocolate)}
.tagline{position:absolute;left:213px;top:258px;font-size:17px;color:var(--accent-pink)}
.scallop{position:absolute;left:145px;top:385px}
.welcome{position:absolute;left:178px;top:496px;font-family:'Parisienne',cursive;font-size:34px;color:var(--heading-blue)}
.lead-pink{position:absolute;left:179px;top:550px;font-size:13px;color:var(--accent-pink)}
.lead-brown{position:absolute;left:179px;top:569px;font-size:13px;color:var(--chocolate)}
.intro{position:absolute;left:179px;top:595px;width:560px;font-size:11px;line-height:16px}
.why{position:absolute;left:178px;top:710px;font-size:23px;color:var(--heading-blue)}
.why-lead{position:absolute;left:182px;top:747px;width:560px;font-size:12.5px;line-height:16px;color:var(--accent-pink)}
.card{position:absolute;top:795px;display:flex;gap:6px}
.card-1{left:185px}.card-2{left:470px}
.card-photo{width:131px;height:105px;border:1px solid #8c7474;background:#fff;padding:3px}
.card-photo div{width:100%;height:100%}
.card h3{font-weight:400;font-size:12.5px;color:var(--chocolate);margin:4px 0 3px}
.card p{font-size:11px;line-height:16px;width:130px}
.panel{position:absolute;left:761px;width:265px;border-radius:4px;color:var(--white)}
.featured{top:493px;height:237px;background:var(--featured)}
.standard{top:734px;height:151px;background:var(--standard)}
.panel h2{position:absolute;left:40px;font-weight:400;font-size:23px}
.featured h2{top:25px}.standard h2{top:25px}
.panel-rule{position:absolute;left:95px;top:13px;width:110px;border-top:1px solid rgba(255,255,255,.6)}
.featured .panel-text{position:absolute;left:40px;top:67px;width:222px;font-size:11.5px;line-height:16px;color:#2a1616}
.featured-photo{position:absolute;left:38px;top:110px;width:100px;height:110px;border-radius:50% 50% 40% 40%;background:radial-gradient(circle at 50% 40%,#e8dcdc 0%,#8a3a4a 45%,#d86a86 80%,rgba(249,170,174,0) 100%)}
.featured-line{position:absolute;left:16px;top:120px;height:95px;border-left:1px solid rgba(255,255,255,.7)}
.featured ul{list-style:none;position:absolute;left:157px;top:108px;width:90px;font-size:11px}
.featured li{height:22px;line-height:22px;border-bottom:1px dashed rgba(255,255,255,.8)}
.featured li:last-child{border-bottom:none}
.standard-photo{position:absolute;left:40px;top:60px;width:89px;height:79px;border:2px solid var(--white);background:linear-gradient(180deg,#8a6a55,#c9a89a 60%,#e8e4e2)}
.standard .panel-text{position:absolute;left:136px;top:64px;width:120px;font-size:11px;line-height:16px}
.standard a{position:absolute;left:140px;top:116px;font-size:10.5px;color:var(--white)}
.connect{position:absolute;left:773px;top:903px;display:flex;align-items:center;gap:6px;font-size:11px;color:#4a3a3a}
.connect span{margin-right:8px}
.social{width:20px;height:20px;border-radius:2px}
.footer-band{position:absolute;left:45px;top:936px;width:1112px;height:65px;background:var(--footer-brown)}
.footer{position:absolute;left:147px;top:943px;width:906px;height:65px;background:var(--footer-inner);box-shadow:0 -2px 4px rgba(0,0,0,.25);color:var(--white);text-align:center;font-size:11.5px}
.footer nav{margin-top:13px}
.footer nav span{margin:0 5px}
.footer p{margin-top:9px;font-size:11px}
</style>
</head>
<body>
<div class="page"></div>

<div class="search"><span>Search</span><div class="search-field"></div><div class="search-go">Go</div></div>

<svg class="ribbon" width="1200" height="115" aria-hidden="true">
  <polygon points="80,64 155,64 155,105 80,105 70,84" fill="#6a434b"/>
  <polygon points="80,64 92,64 92,105 80,105 70,84" fill="#4b2a30"/>
  <polygon points="1045,64 1120,64 1130,84 1120,105 1045,105" fill="#6a434b"/>
  <polygon points="1108,64 1120,64 1130,84 1120,105 1108,105" fill="#4b2a30"/>
</svg>

<div class="nav"><div class="nav-inner"></div>
  <ul>
    <li class="active">Home</li><li>About Us</li><li>Photo gallery</li><li>Flavor Menu</li><li>Products</li><li>Contact</li><li>Enquiry</li>
  </ul>
</div>

<div class="hero">
  <div class="hero-photo" role="img" aria-label="Table of handmade cupcake wrapper and topper materials: paper roses, ribbons, feathers, pearls and scissors"></div>
  <div class="brand"><span class="brand-mark"></span><span class="brand-name">Velvet Ladle Wishes</span></div>
  <div class="tagline">Creating Delicious Works of Art</div>
</div>

<svg class="scallop" width="912" height="90" aria-hidden="true">
  <defs><linearGradient id="band" x1="0" y1="0" x2="0" y2="1"><stop offset="0" stop-color="#fbd0d4"/><stop offset="1" stop-color="#f6b6bc"/></linearGradient></defs>
  <path d="M10,0 H902 L910,72 Q905,80 897,76 Q889,82 881,76 Q873,82 865,76 Q857,82 849,76 Q841,82 833,76 Q825,82 817,76 Q809,82 801,76 Q793,82 785,76 Q777,82 769,76 Q761,82 753,76 Q745,82 737,76 Q729,82 721,76 Q713,82 705,76 Q697,82 689,76 Q681,82 673,76 Q665,82 657,76 Q649,82 641,76 Q633,82 625,76 Q617,82 609,76 Q601,82 593,76 Q585,82 577,76 Q569,82 561,76 Q553,82 545,76 Q537,82 529,76 Q521,82 513,76 Q505,82 497,76 Q489,82 481,76 Q473,82 465,76 Q457,82 449,76 Q441,82 433,76 Q425,82 417,76 Q409,82 401,76 Q393,82 385,76 Q377,82 369,76 Q361,82 353,76 Q345,82 337,76 Q329,82 321,76 Q313,82 305,76 Q297,82 289,76 Q281,82 273,76 Q265,82 257,76 Q249,82 241,76 Q233,82 225,76 Q217,82 209,76 Q201,82 193,76 Q185,82 177,76 Q169,82 161,76 Q153,82 145,76 Q137,82 129,76 Q121,82 113,76 Q105,82 97,76 Q89,82 81,76 Q73,82 65,76 Q57,82 49,76 Q41,82 33,76 Q25,82 17,76 Q9,82 2,72 Z" fill="url(#band)" stroke="#f2a9b0"/>
</svg>

<h1 class="welcome">Welcome to Velvet Ladle Wishes!</h1>
<p class="lead-pink">These cases are perfectly simple and easy to distinguish.</p>
<p class="lead-brown">The wise man therefore always holds in these matters to this principle of selection:</p>
<p class="intro">These cases are perfectly simple and easy to distinguish. In a free hour, when our power of choice is untrammelled and when nothing prevents our being able to do what we like best, every pleasure is to be welcomed and every pain avoided. But in certain circumstances and owing to the claims of duty or the obligations of business it will frequently occur that pleasures have to be repudiated and annoyances accepted. The wise man therefore always holds in these matters to this principle of selection: he rejects pleasures to secure other greater pleasures, or else he endures pains to avoid worse pains</p>

<h2 class="why">Why choose us our bakery?</h2>
<p class="why-lead">These cases are perfectly simple and easy to distinguish.n a free hour, when our power of choice is untrammelled and when nothing prevents</p>

<div class="card card-1">
  <div class="card-photo"><div role="img" aria-label="Tiered stand of pink cupcakes with paper crown toppers" style="background:linear-gradient(180deg,#f3e6e8,#e98aa0 60%,#c6506c)"></div></div>
  <div><h3>At vero eos et accusamus</h3><p>Temporibus autem quibus-dam et aut officiis debitis aut rerum necessitatibus saepe eveniet ut et voluptates repudiandae .</p></div>
</div>
<div class="card card-2">
  <div class="card-photo"><div role="img" aria-label="Cupcake with white frosting and a golden butterfly topper" style="background:radial-gradient(circle at 50% 55%,#f4efe6 0%,#c9a86a 35%,#3e2a20 75%)"></div></div>
  <div><h3>At vero eos et accusamus</h3><p>Temporibus autem quibus-dam et aut officiis debitis aut rerum necessitatibus saepe eveniet ut et voluptates repudiandae .</p></div>
</div>

<section class="panel featured">
  <div class="panel-rule"></div>
  <h2>Featured Category</h2>
  <p class="panel-text">The wise man therefore always holds in these matters to this principle of selection:</p>
  <div class="featured-line"></div>
  <div class="featured-photo" role="img" aria-label="Chocolate cupcake with sprinkles and a white flower topper"></div>
  <ul><li>greater pleasures</li><li>greater pleasures</li><li>greater pleasures</li><li>greater pleasures</li><li>greater pleasures</li></ul>
</section>

<section class="panel standard">
  <div class="panel-rule"></div>
  <h2>Our Standard</h2>
  <div class="standard-photo" role="img" aria-label="Portrait of the head baker"></div>
  <p class="panel-text">The wise man therefore always holds in these matters to this principle</p>
  <a>more</a>
</section>

<div class="connect"><span>Connect with us:</span>
  <div class="social" style="background:#3b5a9a"></div>
  <div class="social" style="background:#5bb6e6"></div>
  <div class="social" style="background:#f07a2a"></div>
  <div class="social" style="background:#1e6fa8"></div>
  <div class="social" style="background:#4a9a4a"></div>
</div>

<div class="footer-band"></div>
<footer class="footer">
  <nav>Home<span>|</span>About Us<span>|</span>Photo gallery<span>|</span>Flavor Menu<span>|</span>Products<span>|</span>Contact<span>|</span>Enquiry</nav>
  <p>© copyrights velvet ladle wishes.All rights Reserved</p>
</footer>
</body>
</html>
```